Business Card Design

We are a company that provides stump grinding services for residential and commercial clients. Looking for a simple business card design that may have some type of graphic on the card that will tie in with the Tamsen name(Grizzly Bear, Paw Print, etc) . Possibly some foliage wrapping around part of the card? Would like to have a simple design that stands out because it is unique. We are working on getting the website set up and there is a simple graphic on the top of the page that came to mind when I mentioned the leaves.

Industry/Entity Type

Business

Contact Information for Business Card

Tamsen Stump Grinding 303-257-4788KodiakStumps.Com

Font styles to use
Serif

Requirements
Must have
• Business name
• Website Address
• Phone Number
Nice to have
• Graphics that would be associated with a Tamsen bear.
Should not have
• Nothing frilly

```html
<!DOCTYPE html>
<html lang="en">
<head>
<meta charset="utf-8">
<title>Tamsen Stump Grinding — Business Card</title>
<link rel="stylesheet" href="https://fonts.googleapis.com/css2?family=Source+Serif+4:opsz,wght@8..60,400;8..60,700&display=swap">
<style>
  :root {
    --card-bg: #ffffff;
    --ink: #333132;
    --mark-grey: #5a5a5a;
    --mark-fade: #f2f2f2;
  }
  html, body {
    margin: 0;
    padding: 0;
    overflow: hidden;
    background: var(--card-bg);
  }
  .card {
    position: relative;
    width: 1200px;
    height: 703px;
    background: var(--card-bg);
    overflow: hidden;
    font-family: "Source Serif 4", Georgia, serif;
    color: var(--ink);
  }
  .paw-graphic {
    position: absolute;
    left: 454px;
    top: 62px;
    width: 290px;
    height: 282px;
    border-radius: 50%;
    background: radial-gradient(ellipse at 50% 55%, var(--mark-grey) 0%, #8a8a8a 45%, var(--mark-fade) 80%, var(--card-bg) 100%);
  }
  .business-name,
  .phone,
  .website {
    position: absolute;
    left: 0;
    width: 100%;
    margin: 0;
    text-align: center;
    line-height: 1;
    white-space: nowrap;
  }
  .business-name {
    top: 394px;
    font-size: 48px;
    font-weight: 700;
  }
  .phone {
    top: 491px;
    font-size: 34px;
    font-weight: 400;
  }
  .website {
    top: 581px;
    font-size: 34px;
    font-weight: 400;
  }
</style>
</head>
<body>
  <main class="card">
    <div class="paw-graphic" role="img" aria-label="Grey bear paw print graphic"></div>
    <h1 class="business-name">Tamsen Stump Grinding</h1>
    <p class="phone">303-555-0146</p>
    <p class="website">TamsenStumps.Com</p>
  </main>
</body>
</html>
```